Business Card Design

We have recently seen two business cards that caught our attention and think the designs would work for us. We are an accounting firm that serves small businesses in a variety of industries. Attached are the two business card that inspired us along with very rough layouts. We would like to see a professional layout using our company information.

Industry/Entity Type

Accounting

Contact Information for Business Card

Company Name - Marlowe Thistle
Address - 4182 Orlanby Lane, Suite 610, Houston, TX 77093
713-555-0187 - Main
281-555-0342 - Fax

Team Member Names, emails and phone numbers (see attachment)

```html
<!DOCTYPE html>
<html lang="en">
<head>
<meta charset="utf-8">
<title>Marlowe Thistle – Business Card</title>
<link rel="stylesheet" href="https://fonts.googleapis.com/css2?family=Lato:wght@400;700;900&display=swap">
<style>
  :root {
    --backdrop: #2a2a2a;
    --card: #f6f6f6;
    --card-shade: #e4e4e4;
    --ink: #111111;
    --muted: #8a8a8a;
    --rule-top: #d0d0d0;
    --rule-bottom: #6a6a6a;
  }
  * { box-sizing: border-box; margin: 0; padding: 0; }
  html, body {
    width: 1200px; height: 900px; overflow: hidden;
    background: var(--backdrop);
    font-family: "Lato", sans-serif;
    color: var(--ink);
  }
  .card {
    position: absolute; left: 75px; top: 150px;
    width: 1050px; height: 600px;
    background: linear-gradient(135deg, var(--card) 0%, #ffffff 45%, var(--card-shade) 100%);
    border-radius: 4px;
  }
  .brand {
    position: absolute; left: 0; right: 0; top: 120px;
    text-align: center;
    font-weight: 900; font-size: 62px; letter-spacing: 1px;
    text-transform: uppercase;
  }
  .divider {
    position: absolute; left: 555px; top: 270px;
    width: 4px; height: 250px;
    background: linear-gradient(var(--rule-top), var(--rule-bottom));
  }
  .contact-person {
    position: absolute; right: 530px; top: 275px;
    text-align: right;
  }
  .person-name {
    font-weight: 900; font-size: 40px; text-transform: uppercase; line-height: 1.05;
  }
  .person-title {
    font-size: 24px; color: var(--muted); margin-bottom: 16px;
  }
  .line {
    display: flex; align-items: center; gap: 10px;
    font-size: 32px; font-weight: 700; line-height: 1.35;
  }
  .contact-person .line { justify-content: flex-end; }
  .line svg { width: 28px; height: 28px; flex: none; fill: var(--ink); }
  .contact-office {
    position: absolute; left: 600px; top: 275px;
  }
  .address {
    font-size: 30px; font-weight: 700; line-height: 1.2; margin: 18px 0 16px;
  }
  .web { font-size: 30px; font-weight: 900; }
  .web .domain { color: var(--muted); }
  .email {
    position: absolute; left: 60px; bottom: 50px;
    font-size: 30px; font-weight: 700;
  }
</style>
</head>
<body>
<main class="card">
  <div class="brand">Marlowe Thistle</div>

  <section class="contact-person">
    <div class="person-name">Odessa Varnell</div>
    <div class="person-title">Account Manager</div>
    <div class="line">
      <svg viewBox="0 0 24 24" aria-hidden="true"><path d="M2 9c0-3 4-5 10-5s10 2 10 5v2h-5V9H7v2H2zM6 12h12l3 8H3z"/></svg>
      713-555-0187
    </div>
    <div class="line">
      <svg viewBox="0 0 24 24" aria-hidden="true"><path d="M7 1h10a2 2 0 0 1 2 2v18a2 2 0 0 1-2 2H7a2 2 0 0 1-2-2V3a2 2 0 0 1 2-2zm0 2v16h10V3z"/></svg>
      832-555-0129
    </div>
  </section>

  <div class="divider"></div>

  <section class="contact-office">
    <div class="line">
      <svg viewBox="0 0 24 24" aria-hidden="true"><path d="M2 9c0-3 4-5 10-5s10 2 10 5v2h-5V9H7v2H2zM6 12h12l3 8H3z"/></svg>
      713-555-0187
    </div>
    <div class="line">
      <svg viewBox="0 0 24 24" aria-hidden="true"><path d="M6 2h12v6H6zM3 9h18v9h-3v4H6v-4H3zm5 6v5h8v-5z"/></svg>
      281-555-0342
    </div>
    <div class="address">4182 Orlanby Lane, Suite 610,<br>Houston, TX 77093</div>
    <div class="web">www.<span class="domain">marlowethistle</span>.com</div>
  </section>

  <div class="email line">
    <svg viewBox="0 0 24 24" aria-hidden="true"><path d="M2 5h20v14H2zm2 2v.5l8 6 8-6V7zm0 3v7h16v-7l-8 6z"/></svg>
    ovarnell@marlowethistle.com
  </div>
</main>
</body>
</html>
```